114" Wide by 92" Tall Display for Trade Show Booth or Backdrop

Morwick is a financial services business helping our clients recover money from their customers. There are thousands of companies like ours and we frequently attend trade shows to attract new clients but really need graphic design that will really catch people's eye and help us stand out from the crowd.
Our colors, as our logo shows, are blue and green.
Catching attention is our first focus so we will choose the most eye catching and appealing graphics and then find a way to create marketing around it.
EXAMPLE 1: If there is a graphic of the keyhole, then we might create a marketing tagline like this one: "Morwick has the Key to increased profits". EXAMPLE 2: If there is a graphic of something fast like a race car, a jet, a cheetah or a locomotive, then we might create a marketing tagline like this one: "Morwick is the fastest way to recover your receivables". EXAMPLE 3: If there is a graphic of a butterfly, then we might create a marketing tagline like this one: "Morwick transforms your receivables into cash". EXAMPLE 4: If there is a graphic of a road, trail or path, then we might create a marketing tagline like this one: "Morwick is the best path to recover your receivables".
NONE OF THE EXAMPLES NEED TO BE USED, THEY ARE JUST FOR ILLUSTRATION PURPOSES OF HOW WE CAN CREATE A MESSAGE FOR ANYTHING YOU DESIGN.

The winning design would make someone who sees it from 30 meters away want to get a closer look.

Target Market(s)

Executives in Finance at Colleges and Universities, Banks, Healthcare, Credit Card, Auto Finance etc.

Industry/Entity Type

Financial Service

Font styles to use
Sans Serif

Colors
abd037
3276b5

Requirements
Must have
• What I really want is:
• 1) Our company name logo to run the top 10-20% of backdrop.
• 2) Eye catching image in the middle 60-70% of backdrop and
• 3) Ancillary, non-necessary info at the bottom 10-20% of backdrop
• During some events this backdrop might have a table in front of it causing the bottom third of the backdrop to not be seen from a distance which is why I want the above format.
Nice to have
• A powerful image that catches someone's eye from across the room and makes them want to get a closer look. The worst thing at a trade show is to blend in with the crowd so we definitely want to stand out. Something that works with our branding and colors would be nice. Some designers have used some optical illusions, mazes, tunnels and other interesting shapes.
Should not have
• Anything that can be construed as negative, bad or makes people uncomfortable or reflects poorly on the company.
• NO ADDRESSES OR PHONE NUMBERS ON DESIGN!!
• NO SENTENCES OR BUNCH OF WORDS ON DESIGN!!!

```html
<!DOCTYPE html>
<html lang="en">
<head>
<meta charset="utf-8">
<title>Morwick Trade Show Backdrop</title>
<link rel="stylesheet" href="https://fonts.googleapis.com/css2?family=Oswald:wght@600;700&family=Raleway:wght@300;400&display=swap">
<style>
  :root {
    --stage: #3a3a3c;
    --brand-blue: #0a4fa3;
    --brand-green: #a6c84a;
    --paper: #ffffff;
    --ink: #111111;
    --photo-light: #eef0ec;
    --photo-mid: #c9cfc4;
  }
  html, body {
    margin: 0;
    padding: 0;
    width: 1200px;
    height: 1200px;
    overflow: hidden;
    background: var(--stage);
  }
  .canvas {
    position: relative;
    width: 1200px;
    height: 1200px;
  }
  .backdrop {
    position: absolute;
    left: 87px;
    top: 186px;
    width: 1026px;
    height: 827px;
    display: block;
  }
  .wordmark {
    font-family: "Raleway", sans-serif;
    font-weight: 400;
    font-size: 33px;
    letter-spacing: 12px;
    fill: var(--ink);
  }
  .slogan {
    font-family: "Raleway", sans-serif;
    font-weight: 400;
    font-size: 30px;
    fill: var(--paper);
  }
  .tagline {
    font-family: "Oswald", sans-serif;
    font-weight: 700;
    font-size: 50px;
    fill: var(--brand-blue);
  }
  .service-label {
    font-family: "Oswald", sans-serif;
    font-weight: 600;
    font-size: 22px;
    fill: var(--brand-blue);
    text-anchor: middle;
  }
</style>
</head>
<body>
<main class="canvas">
  <svg class="backdrop" viewBox="109 232 1282 1034" xmlns="http://www.w3.org/2000/svg">
    <defs>
      <linearGradient id="photoTone" x1="0" y1="0" x2="1" y2="1">
        <stop offset="0" stop-color="var(--photo-light)"/>
        <stop offset="1" stop-color="var(--photo-mid)"/>
      </linearGradient>
    </defs>

    <!-- body -->
    <rect class="body-field" x="109" y="232" width="1282" height="1034" fill="var(--paper)"/>

    <!-- header band -->
    <g class="header">
      <rect x="109" y="232" width="1282" height="185" fill="var(--brand-blue)"/>
      <polygon points="109,232 515,232 660,405 109,405" fill="var(--brand-green)"/>
      <polygon points="537,232 560,232 703,403 680,403" fill="var(--brand-green)"/>
      <rect class="brand-square" x="241" y="251" width="73" height="72" fill="var(--brand-blue)"/>
      <text class="wordmark" x="176" y="377">MORWICK</text>
      <text class="slogan" x="716" y="311">A CREATIVE APPROACH</text>
      <text class="slogan" x="906" y="349">TO CUSTOMER CONTACT</text>
    </g>

    <!-- hero -->
    <g class="hero-photo" role="img" aria-label="Photo: businesswoman catching falling dollar bills with a butterfly net">
      <rect x="740" y="417" width="540" height="620" fill="url(#photoTone)"/>
    </g>
    <text class="tagline" x="204" y="697">Your Marketing tagline</text>
    <text class="tagline" x="204" y="801">Your Marketing tagline</text>

    <!-- footer band -->
    <g class="footer">
      <rect x="109" y="1095" width="1231" height="12" fill="var(--brand-blue)"/>
      <polygon points="109,1107 1060,1107 1170,1266 109,1266" fill="var(--brand-green)"/>
      <polygon points="1052,1095 1340,1095 1340,1093 1391,1093 1391,1266 1170,1266" fill="var(--brand-blue)"/>
    </g>

    <!-- service badges -->
    <g class="services" fill="var(--brand-green)" stroke="var(--brand-blue)" stroke-width="8">
      <circle cx="323" cy="1101" r="81"/>
      <circle cx="608" cy="1101" r="81"/>
      <circle cx="892" cy="1101" r="81"/>
      <circle cx="1177" cy="1097" r="79"/>
    </g>
    <text class="service-label" x="318" y="1080">Debt</text>
    <text class="service-label" x="318" y="1108">Recovery</text>
    <text class="service-label" x="318" y="1136">Service</text>
    <text class="service-label" x="608" y="1080">Customer</text>
    <text class="service-label" x="608" y="1108">Lifecycle</text>
    <text class="service-label" x="608" y="1136">Support</text>
    <text class="service-label" x="892" y="1080">Accounts</text>
    <text class="service-label" x="892" y="1108">Receivable</text>
    <text class="service-label" x="892" y="1136">Outsourcing</text>
    <text class="service-label" x="1177" y="1085">Fraud</text>
    <text class="service-label" x="1177" y="1113">Management</text>
  </svg>
</main>
</body>
</html>
```